Emergency Dental Referral Company

I need a brochure to advertise my business to prospective dentists that may want to join or to dentists that may want to use this for their own patients. I also need to advertise this brochure to ER physicians who see many dental emergencies. This brochure is meant to be dual purpose: advertise our company and services to the ER physicians who then hand out the brochures to the dental emergency patients in pain. See our website for further details at www.vellumcrestora.com

I will also be attaching our logo design.

Target Market(s)

Emergency Room physicians and other medical personnel who will distribute these brochures to patients in dental pain and dental emergencies

Industry/Entity Type

Business

Font styles to use
Serif
Sans Serif

Requirements
Must have
• Must be simple! Must have a call to action- inspiration to go to website. Highlight our guarantee that states "If you are not seen by a dentist in 24 hours or less, you will receive your money back. Emphasis on the logo. Must discuss how we find a dentist in your zip code in three easy steps.
• For the color- please make similar to our website of www.vellumcrestora.com
Nice to have
• Would like to state that this service can see patients at any hour of the day.
Should not have
• no contact information besides the URL. www.vellumcrestora.com

```html
<!DOCTYPE html>
<html lang="en">
<head>
<meta charset="utf-8">
<title>Vellum Crestora Brochure</title>
<link rel="stylesheet" href="https://fonts.googleapis.com/css2?family=Didact+Gothic&display=swap">
<style>
  :root {
    --backdrop: #dcdcdc;
    --paper: #ffffff;
    --paper-shade: #f1f1f1;
    --brand-blue: #1a6fb8;
    --brand-blue-light: #3aa0dc;
    --brand-green: #3fa441;
    --brand-green-light: #8cc63f;
    --ink: #2a2a2a;
    --ink-soft: #6a6a6a;
    --photo-mouth-a: #e9c9c4;
    --photo-mouth-b: #b8b8b8;
    --photo-face-a: #e8e8ea;
    --photo-face-b: #d9b39b;
  }
  * { margin: 0; padding: 0; box-sizing: border-box; }
  html, body {
    width: 1200px; height: 847px; overflow: hidden;
    background: var(--backdrop);
    font-family: "Didact Gothic", "Century Gothic", sans-serif;
  }
  .brochure {
    position: absolute; left: 190px; top: 140px;
    display: flex; width: 820px; height: 567px;
    box-shadow: 0 18px 40px rgba(0,0,0,.25);
  }
  .page {
    position: relative; width: 410px; height: 567px;
    background: var(--paper); overflow: hidden;
  }
  .page--inside { background: linear-gradient(90deg, var(--paper) 70%, var(--paper-shade)); }
  .page-art { position: absolute; inset: 0; width: 100%; height: 100%; }

  /* inside panel */
  .steps-title {
    position: absolute; left: 108px; top: 78px;
    font-size: 14px; color: var(--brand-blue-light); font-weight: 400;
  }
  .steps-copy {
    position: absolute; left: 108px; top: 100px; width: 210px;
    font-size: 8.5px; line-height: 1.55; color: var(--ink-soft);
  }
  .mouth-photo {
    position: absolute; left: 118px; top: 228px; width: 200px; height: 228px;
    border: 4px solid var(--brand-green);
    background: linear-gradient(160deg, var(--photo-mouth-a), var(--photo-mouth-b));
  }
  .site-url {
    position: absolute; left: 116px; top: 478px;
    font-size: 16px; color: var(--brand-blue); letter-spacing: .5px;
  }

  /* cover panel */
  .brand {
    position: absolute; left: 28px; top: 36px;
    display: flex; align-items: center; gap: 8px;
  }
  .brand-mark { width: 14px; height: 14px; background: var(--brand-blue); }
  .brand-name { font-size: 17px; color: var(--brand-blue); }
  .guarantee {
    position: absolute; left: 40px; top: 128px; width: 150px;
    text-align: right; font-size: 19px; line-height: 1.05; color: var(--ink);
  }
  .guarantee-hours { display: block; color: var(--brand-green); font-size: 23px; }
  .patient-photo {
    position: absolute; right: 0; top: 48px; width: 210px; height: 410px;
    background: radial-gradient(ellipse at 45% 40%, var(--photo-face-b) 0%, var(--photo-face-a) 65%);
  }
</style>
</head>
<body>
  <main class="brochure">
    <section class="page page--inside">
      <svg class="page-art" viewBox="0 0 410 567" preserveAspectRatio="none" aria-hidden="true">
        <defs>
          <linearGradient id="insideTop" x1="0" y1="0" x2="1" y2="0">
            <stop offset="0" stop-color="#1a6fb8"/><stop offset="1" stop-color="#3aa0dc" stop-opacity="0"/>
          </linearGradient>
          <linearGradient id="insideBottom" x1="0" y1="1" x2="1" y2="0">
            <stop offset="0" stop-color="#8cc63f" stop-opacity="0"/><stop offset="1" stop-color="#3fa441"/>
          </linearGradient>
        </defs>
        <path d="M0 0 H230 Q90 20 0 120 Z" fill="url(#insideTop)"/>
        <path d="M410 330 V567 H200 Q330 520 410 330 Z" fill="url(#insideBottom)"/>
      </svg>
      <h2 class="steps-title">Class Aptent Taciti Soci Ad Litora</h2>
      <p class="steps-copy">Tell us your zip code, describe your dental pain, and choose a time that suits you. Our network finds a nearby dentist ready to see you at any hour of the day or night. Fast, simple care when you need it most, with our guarantee.</p>
      <div class="mouth-photo" role="img" aria-label="Close-up photo of an open mouth with dental extraction forceps on a tooth"></div>
      <p class="site-url">www.vellumcrestora.com</p>
    </section>

    <section class="page page--cover">
      <div class="patient-photo" role="img" aria-label="Photo of a young man holding his jaw in tooth pain"></div>
      <svg class="page-art" viewBox="0 0 410 567" preserveAspectRatio="none" aria-hidden="true">
        <defs>
          <linearGradient id="coverBand" x1="0" y1="0" x2="1" y2="0">
            <stop offset="0" stop-color="#1a6fb8"/><stop offset=".55" stop-color="#3aa0dc"/><stop offset="1" stop-color="#3fa441"/>
          </linearGradient>
        </defs>
        <path d="M0 0 H410 V36 Q220 6 0 22 Z" fill="url(#coverBand)"/>
        <path d="M0 22 Q220 6 410 36 V50 Q220 18 0 30 Z" fill="#ffffff"/>
        <path d="M0 450 Q180 500 410 470 V567 H0 Z" fill="#ffffff"/>
        <path d="M0 470 Q190 520 410 490 V567 H0 Z" fill="url(#coverBand)"/>
        <path d="M0 490 Q190 545 410 515 V567 H0 Z" fill="#1a6fb8" opacity=".55"/>
      </svg>
      <div class="brand">
        <span class="brand-mark"></span>
        <span class="brand-name">Vellum Crestora</span>
      </div>
      <p class="guarantee">If you are not seen by a dentist in <span class="guarantee-hours">24 hours</span> or less, you will receive your money back</p>
    </section>
  </main>
</body>
</html>
```